Brevlon Website Design - Wordpress

Need a website WordPress design for our existing website that we just stood up. The logo is already in place and name. Brevlon.example We are a company which makes connections with our clients through educating them and providing networking events. We would like for the website to show a VIP/special feel to it.

Target Market(s)

Business executives and employees. Age group 26-65 in the following sectors:
- Technology
- Human Resources
- Finance
- Sales

Industry/Entity Type

Technical Service

Number of Pages Required

4 page

Font styles to use
Sans Serif

Requirements
Must have
• Must be something for Wordpress
Nice to have
• Would like this to be professional but look cutting edge and VIP.

```html
<!DOCTYPE html>
<html lang="en">
<head>
<meta charset="utf-8">
<title>Brevlon — Connected</title>
<link rel="stylesheet" href="https://fonts.googleapis.com/css2?family=Mulish:wght@300;400;600;700&display=swap">
<style>
:root{
  --ink:#2b2b2b;
  --muted:#6f6f6f;
  --night:#111820;
  --footer:#1b1b1b;
  --red:#c8202a;
  --green:#3aa335;
  --blue:#1e5a8c;
  --purple:#6a2c7c;
  --yellow:#e0a626;
  --orange:#e8912a;
  --paper:#ffffff;
  --mist:#f1f1f1;
}
*{margin:0;padding:0;box-sizing:border-box}
html,body{width:1200px;height:3673px;overflow:hidden}
body{position:relative;font-family:'Mulish',Arial,sans-serif;color:var(--ink);background:var(--paper)}
.abs{position:absolute}

/* hero */
.hero{position:absolute;left:0;top:0;width:1200px;height:790px;background:var(--night);overflow:hidden}
.hero-visual{position:absolute;left:0;top:190px;width:700px;height:420px;background:radial-gradient(ellipse at 20% 45%,rgba(230,60,60,.55),transparent 45%),linear-gradient(90deg,rgba(40,70,180,.35),rgba(200,40,60,.35) 60%,rgba(17,24,32,0));}
.brand{position:absolute;left:112px;top:52px;display:flex;align-items:center;gap:14px}
.brand-mark{width:26px;height:26px;background:var(--red)}
.brand-name{color:#fff;font-size:38px;font-weight:400;letter-spacing:7px}
.nav{position:absolute;top:62px;left:658px;display:flex;gap:36px;color:#fff;font-size:18px}
.search{position:absolute;left:1068px;top:66px}
.hero-title{position:absolute;left:732px;top:268px;color:#fff;font-size:47px;font-weight:300;line-height:60px}
.hero-text{position:absolute;left:734px;top:400px;width:360px;color:#d8d8d8;font-size:16px;line-height:27px}
.btn{display:inline-block;font-size:13px;text-transform:uppercase;text-decoration:none}
.hero-btn{position:absolute;left:734px;top:488px;width:136px;height:42px;line-height:42px;text-align:center;background:var(--red);color:#fff}

/* offer */
.section-title{position:absolute;width:1200px;text-align:center;font-weight:300;font-size:38px;letter-spacing:1px}
.divider{position:absolute;left:540px;width:120px;height:2px;background:linear-gradient(90deg,transparent,#bbb,transparent)}
.divider::after{content:"";position:absolute;left:54px;top:-6px;width:12px;height:12px;background:var(--purple);transform:rotate(45deg)}
.offer{position:absolute;top:960px;width:230px;text-align:center}
.offer-icon{width:124px;height:124px;margin:0 auto;border-radius:50%;background:#fff;box-shadow:0 0 0 6px #f1f1f1,0 4px 12px rgba(0,0,0,.12);display:flex;align-items:center;justify-content:center}
.offer-label{margin-top:36px;font-size:18px;font-weight:700;letter-spacing:1px}
.offer-text{margin-top:12px;font-size:13px;line-height:25px;color:var(--muted)}
.chev{margin-top:6px}
.value-btn{position:absolute;left:507px;top:1318px;width:186px;height:53px;line-height:53px;text-align:center;background:var(--green);color:#fff;font-size:18px;font-weight:600}

/* strategy */
.strategy-bg{position:absolute;left:0;top:1470px}
.strategy-sub{position:absolute;top:1670px;width:1200px;text-align:center;font-size:17px;color:var(--muted)}
.note{position:absolute;width:280px;font-size:13px;line-height:25px;color:var(--muted)}
.note.right{text-align:right}
.pill{position:absolute;width:112px;height:38px;line-height:34px;border:2px solid;border-radius:20px;text-align:center;font-size:13px;background:#fff}

/* about */
.about-title{position:absolute;left:120px;top:2632px;font-size:38px;font-weight:300}
.about-div{position:absolute;left:120px;top:2714px;width:140px;height:2px;background:linear-gradient(90deg,#bbb,transparent)}
.about-div::after{content:"";position:absolute;left:58px;top:-6px;width:12px;height:12px;background:var(--purple);transform:rotate(45deg)}
.about-text{position:absolute;left:120px;top:2762px;width:480px;font-size:15px;line-height:35px;color:var(--muted)}
.about-btn{position:absolute;left:120px;top:3007px;width:148px;height:49px;line-height:49px;text-align:center;background:var(--green);color:#fff;font-weight:600}
.about-photo{position:absolute;left:642px;top:2640px;width:467px;height:441px;background:linear-gradient(135deg,#2c6fb4,#7fb0d8 45%,#d8b08e 75%,#8a5a3c)}

/* footer */
.footer{position:absolute;left:0;top:3140px;width:1200px;height:533px;background:var(--footer)}
.footer-brand{position:absolute;left:0;top:3380px;width:1200px;display:flex;justify-content:center;align-items:center;gap:16px}
.footer-brand .brand-name{font-size:44px}
.contact{position:absolute;top:3508px;display:flex;align-items:center;gap:16px;color:#eee;font-size:13px;line-height:22px}
.contact-ico{width:44px;height:44px;border:2px solid #fff;border-radius:50%;display:flex;align-items:center;justify-content:center}
.copy{position:absolute;left:98px;top:3628px;color:#ddd;font-size:12px}
.social{position:absolute;left:968px;top:3620px;display:flex;gap:10px}
.social span{width:26px;height:26px;border:1px solid #ccc;border-radius:50%}
</style>
</head>
<body>

<header class="hero">
  <div class="hero-visual" role="img" aria-label="Data network visual of coloured points connected by flowing red and blue lines"></div>
  <div class="brand"><span class="brand-mark"></span><span class="brand-name">BREVLON</span></div>
  <nav class="nav"><span>Events</span><span>Expand</span><span>X</span><span>About</span><span>Connect</span></nav>
  <svg class="search" width="18" height="18" viewBox="0 0 18 18"><circle cx="7" cy="7" r="5.5" fill="none" stroke="#3aa335" stroke-width="2.5"/><line x1="11" y1="11" x2="16" y2="16" stroke="#3aa335" stroke-width="2.5"/></svg>
  <h1 class="hero-title">EXPAND YOUR<br>BUSINESS</h1>
  <p class="hero-text">Sed ut perspiciatis unde omnis iste natus error sit voluptatem accusantium</p>
  <a class="btn hero-btn">Read more ▸</a>
  <svg class="abs" style="left:0;top:0" width="1200" height="790">
    <polygon points="0,790 0,775 737,628 1200,740 1200,790" fill="#fff"/>
    <polyline points="330,710 737,628 1010,694" fill="none" stroke="#3aa335" stroke-width="5"/>
    <circle cx="737" cy="622" r="24" fill="#fff" stroke="#ddd"/>
    <polyline points="728,612 737,621 746,612" fill="none" stroke="#111820" stroke-width="2.5"/>
    <polyline points="728,622 737,631 746,622" fill="none" stroke="#111820" stroke-width="2.5"/>
  </svg>
</header>

<h2 class="section-title" style="top:782px">WHAT WE OFFER YOU</h2>
<div class="divider" style="top:872px"></div>

<div class="offer" style="left:88px">
  <div class="offer-icon"><svg width="60" height="50" viewBox="0 0 60 50"><polygon points="30,4 58,16 30,28 2,16" fill="#1e5a8c"/><path d="M14 22v12c8 6 24 6 32 0V22l-16 7z" fill="#163f63"/><line x1="54" y1="17" x2="54" y2="34" stroke="#e0a626" stroke-width="2"/></svg></div>
  <div class="offer-label">EDUCATE</div>
  <p class="offer-text">At BREVLON, we provide effective training and learning as the foundation for building</p>
  <svg class="chev" width="14" height="14" viewBox="0 0 14 14"><polyline points="2,2 7,7 12,2" fill="none" stroke="#3aa335" stroke-width="2"/><polyline points="2,7 7,12 12,7" fill="none" stroke="#3aa335" stroke-width="2"/></svg>
</div>
<div class="offer" style="left:353px">
  <div class="offer-icon"><svg width="56" height="56" viewBox="0 0 56 56"><line x1="10" y1="10" x2="46" y2="46" stroke="#c8202a" stroke-width="7" stroke-linecap="round"/><line x1="46" y1="10" x2="10" y2="46" stroke="#c8202a" stroke-width="7" stroke-linecap="round"/></svg></div>
  <div class="offer-label">EQUIP</div>
  <p class="offer-text">Through our connected ecosystem of companies, we'll help find the right partners</p>
  <svg class="chev" width="14" height="14" viewBox="0 0 14 14"><polyline points="2,2 7,7 12,2" fill="none" stroke="#3aa335" stroke-width="2"/><polyline points="2,7 7,12 12,7" fill="none" stroke="#3aa335" stroke-width="2"/></svg>
</div>
<div class="offer" style="left:617px">
  <div class="offer-icon"><svg width="56" height="44" viewBox="0 0 56 44"><path d="M6 14h40M36 4l10 10-10 10M50 30H10M20 20 10 30l10 10" fill="none" stroke="#6a2c7c" stroke-width="5"/></svg></div>
  <div class="offer-label">EXCHANGE</div>
  <p class="offer-text">We connect you with others who have successfully implemented our X Strategy to facilitate</p>
  <svg class="chev" width="14" height="14" viewBox="0 0 14 14"><polyline points="2,2 7,7 12,2" fill="none" stroke="#3aa335" stroke-width="2"/><polyline points="2,7 7,12 12,7" fill="none" stroke="#3aa335" stroke-width="2"/></svg>
</div>
<div class="offer" style="left:882px">
  <div class="offer-icon"><svg width="52" height="52" viewBox="0 0 52 52"><path d="M22 10H8v34h34V30" fill="none" stroke="#e8912a" stroke-width="5"/><path d="M22 30 44 8M30 8h14v14" fill="none" stroke="#e8912a" stroke-width="5"/></svg></div>
  <div class="offer-label">EXPAND</div>
  <p class="offer-text">Our goal is to help you and your business increase productivity and scale through effective</p>
  <svg class="chev" width="14" height="14" viewBox="0 0 14 14"><polyline points="2,2 7,7 12,2" fill="none" stroke="#3aa335" stroke-width="2"/><polyline points="2,7 7,12 12,7" fill="none" stroke="#3aa335" stroke-width="2"/></svg>
</div>
<a class="btn value-btn" style="text-transform:none">X = VALUE</a>

<svg class="strategy-bg" width="1200" height="990" viewBox="0 0 1200 990"><polygon points="0,75 600,0 1200,75 1200,910 600,985 0,910" fill="#f1f1f1"/></svg>
<h2 class="section-title" style="top:1598px">IT'S ABOUT OUR UNIQUE X STRATEGY</h2>
<p class="strategy-sub">BREVLON provides impactful connection opportunities to help educate, equip and expand you and your business</p>
<div class="divider" style="top:1736px"></div>

<svg class="abs" style="left:340px;top:1840px" width="520" height="530" viewBox="340 1840 520 530">
  <g font-family="Mulish,Arial,sans-serif" text-anchor="middle" fill="#fff">
    <polygon points="600,1868 710,1978 600,2088 490,1978" fill="#1e5a8c"/>
    <polygon points="472,1996 582,2106 472,2216 362,2106" fill="#6a2c7c"/>
    <polygon points="728,1996 838,2106 728,2216 618,2106" fill="#c8202a"/>
    <polygon points="600,2124 710,2234 600,2344 490,2234" fill="#e0a626"/>
    <text x="600" y="1980" font-size="22">MIND</text><text x="600" y="2006" font-size="11">thought</text>
    <text x="476" y="2104" font-size="22">Soul</text><text x="476" y="2130" font-size="11">intuition</text>
    <text x="724" y="2100" font-size="22">Heart</text><text x="724" y="2126" font-size="11">emotions</text>
    <text x="600" y="2224" font-size="22">Strength</text><text x="600" y="2250" font-size="11">Energy</text>
  </g>
  <circle cx="600" cy="2106" r="50" fill="#fff" stroke="#e4e4e4" stroke-width="4"/>
  <g fill="#fff" stroke="#e4e4e4" stroke-width="3">
    <circle cx="600" cy="1880" r="30"/><circle cx="370" cy="2106" r="30"/><circle cx="832" cy="2106" r="30"/><circle cx="600" cy="2335" r="30"/>
  </g>
  <circle cx="600" cy="1880" r="12" fill="#1e5a8c"/>
  <rect x="365" y="2092" width="10" height="28" rx="4" fill="#6a2c7c"/>
  <path d="M832 2120l-12-12a7 7 0 0 1 12-9 7 7 0 0 1 12 9z" fill="#c8202a"/>
  <circle cx="600" cy="2335" r="11" fill="none" stroke="#e0a626" stroke-width="5"/>
</svg>

<p class="note" style="left:710px;top:1812px">Sed ut perspiciatis unde omnis iste natus error sit voluptatem accusantium doloremque laudantiumeaque ipsa quae.</p>
<a class="pill" style="left:710px;top:1910px;border-color:var(--blue);color:var(--blue)">READ MORE</a>
<p class="note right" style="left:129px;top:1898px">Sed ut perspiciatis unde omnis iste natus error sit voluptatem accusantium doloremque laudantiumeaque ipsa quae..</p>
<a class="pill" style="left:296px;top:1995px;border-color:var(--purple);color:var(--purple)">READ MORE</a>
<p class="note" style="left:793px;top:2176px">Sed ut perspiciatis unde omnis iste natus error sit voluptatem accusantium doloremque laudantiumeaque ipsa quae..</p>
<a class="pill" style="left:793px;top:2272px;border-color:var(--red);color:var(--red)">READ MORE</a>
<p class="note right" style="left:208px;top:2262px">Sed ut perspiciatis unde omnis iste natus error sit voluptatem accusantium doloremque laudantiumeaque ipsa quae..</p>
<a class="pill" style="left:375px;top:2355px;border-color:var(--yellow);color:var(--yellow)">READ MORE</a>

<h2 class="about-title">ABOUT US</h2>
<div class="about-div"></div>
<p class="about-text">Sed ut perspiciatis unde omnis iste natus error sit voluptatem accusantium doloremque laudantium, totam rem aperiam, eaque ipsa quae ab illo inventore veritatis et quasi architecto beatae vitae dicta sunt quia consequuntur magni dolores eos qui ratione olor sit amet, consectetur, adipisci velit, sed quia non numquam eius modi tempora incidunt ut labore aliquam quaerat voluptatem</p>
<a class="btn about-btn">Read more ➜</a>
<div class="about-photo" role="img" aria-label="Photo of a hand touching a screen with social reaction icons floating above"></div>

<footer class="footer"></footer>
<svg class="abs" style="left:0;top:3140px" width="1200" height="170">
  <polygon points="0,0 1200,0 600,160" fill="#fff"/>
  <polyline points="200,107 600,160 1000,107" fill="none" stroke="#3aa335" stroke-width="5"/>
</svg>
<div class="footer-brand"><span class="brand-mark" style="width:30px;height:30px"></span><span class="brand-name">BREVLON</span></div>

<div class="contact" style="left:215px">
  <span class="contact-ico"><svg width="16" height="20" viewBox="0 0 16 20"><path d="M8 19S1 11 1 7a7 7 0 0 1 14 0c0 4-7 12-7 12z" fill="#fff"/><circle cx="8" cy="7" r="2.5" fill="#1b1b1b"/></svg></span>
  <span>At vero eos et accu<br>samus et iusto odio dimos ducimu</span>
</div>
<div class="contact" style="left:544px">
  <span class="contact-ico"><svg width="18" height="18" viewBox="0 0 18 18"><path d="M4 1l3 4-2 2c1 3 3 5 6 6l2-2 4 3-2 3C8 17 1 10 1 3z" fill="#fff"/></svg></span>
  <span>Phone: 1-855-555-0142</span>
</div>
<div class="contact" style="left:762px">
  <span class="contact-ico"><svg width="20" height="14" viewBox="0 0 20 14"><rect width="20" height="14" rx="2" fill="#fff"/><polyline points="1,1 10,8 19,1" fill="none" stroke="#1b1b1b" stroke-width="1.5"/></svg></span>
  <span>Email: connect@brevlon.example</span>
</div>

<p class="copy">Copyrights © 2019, Companyname. All rights reserved.</p>
<div class="social"><span></span><span></span><span></span><span></span></div>

</body>
</html>
```